Colin Vardek Business card

Hey there, I’m hoping to have a business card designed. I’m in Real estate and just switched to a new Brokerage called: The Harbourline Property Group

The back could just be the company name maybe or whatever looks good!

I’ve attached some logos of our company and some cards my buddy had done up.

On the card:
Colin Vardek
colinvardek@mailora.com
587-412-9065
colinvardek.ca

Target Market(s)

Home buyers and sellers

Industry/Entity Type

Real Estate

Contact Information for Business Card

just looking for a cool and modern design with my picture on it. I like the idea of Black and red being used.

Requirements
Must have
• all the details provided. I'm open to anything. Just want a professional looking card.

```html
<!DOCTYPE html>
<html lang="en">
<head>
<meta charset="utf-8">
<title>Colin Vardek – Business Card</title>
<link href="https://fonts.googleapis.com/css2?family=Poppins:wght@300;400;600;700;800&display=swap" rel="stylesheet">
<style>
  :root {
    --backdrop: #232224;
    --card-black: #1f1e21;
    --emboss: #141315;
    --brand-red: #d0223d;
    --paper-white: #ffffff;
    --text-white: #f4f4f4;
    --text-soft: #e6e6e6;
  }
  * { box-sizing: border-box; margin: 0; padding: 0; }
  html, body {
    width: 1200px; height: 711px; overflow: hidden;
    background: var(--backdrop);
    font-family: "Poppins", sans-serif;
  }
  .canvas {
    position: relative; width: 1200px; height: 711px;
    display: flex; align-items: center; justify-content: center; gap: 40px;
  }
  .card {
    position: relative; width: 520px; height: 300px;
    border-radius: 18px; overflow: hidden;
    background: var(--card-black);
    box-shadow: 0 0 0 2px var(--brand-red), 0 14px 30px rgba(0,0,0,.55);
  }
  /* Back */
  .card-back { display: flex; align-items: center; justify-content: center; }
  .back-name {
    width: 360px; text-align: center;
    font-weight: 800; font-size: 34px; line-height: 1.1;
    text-transform: uppercase; letter-spacing: .5px;
    color: var(--emboss);
  }
  /* Front */
  .front-art { position: absolute; inset: 0; }
  .front-brand {
    position: absolute; left: 28px; top: 28px;
    width: 230px;
    font-weight: 800; font-size: 17px; line-height: 1.15; letter-spacing: .3px;
    text-transform: uppercase; color: var(--text-white);
    display: flex; align-items: center; gap: 10px;
  }
  .brand-dot { width: 12px; height: 12px; border-radius: 50%; background: var(--brand-red); flex: none; }
  .name-bar {
    position: absolute; left: 0; top: 140px;
    width: 9px; height: 30px; background: var(--brand-red);
  }
  .agent-name {
    position: absolute; left: 22px; top: 134px;
    font-size: 28px; line-height: 1.3; color: var(--text-white); white-space: nowrap;
  }
  .agent-name .first { font-weight: 700; color: var(--brand-red); }
  .agent-name .last { font-weight: 300; }
  .contact-list {
    position: absolute; left: 28px; top: 212px;
    list-style: none; display: flex; flex-direction: column; gap: 5px;
  }
  .contact-item {
    display: flex; align-items: center; gap: 8px;
    font-size: 12px; font-weight: 400; color: var(--text-soft); white-space: nowrap;
  }
  .contact-icon { width: 12px; height: 12px; flex: none; }
</style>
</head>
<body>
<main class="canvas">

  <section class="card card-back" aria-label="Card back">
    <p class="back-name">The Harbourline Property Group</p>
  </section>

  <section class="card card-front" aria-label="Card front">
    <svg class="front-art" viewBox="0 0 520 300" width="520" height="300">
      <circle cx="545" cy="60" r="262" fill="var(--brand-red)"/>
      <circle cx="520" cy="30" r="240" fill="var(--paper-white)"/>
      <defs>
        <linearGradient id="portraitTone" x1="0" y1="0" x2="0" y2="1">
          <stop offset="0" stop-color="#ffffff"/>
          <stop offset=".55" stop-color="#e9e2dc"/>
          <stop offset="1" stop-color="#3a3d44"/>
        </linearGradient>
      </defs>
      <g role="img" aria-label="Portrait photo of Colin Vardek in a dark blazer and white shirt">
        <circle cx="520" cy="30" r="240" fill="url(#portraitTone)"/>
      </g>
    </svg>

    <div class="front-brand"><span class="brand-dot"></span><span>The Harbourline<br>Property Group</span></div>

    <div class="name-bar"></div>
    <h1 class="agent-name"><span class="first">Colin</span> <span class="last">Vardek</span></h1>

    <ul class="contact-list">
      <li class="contact-item">
        <svg class="contact-icon" viewBox="0 0 24 24"><path fill="var(--brand-red)" d="M6.6 10.8a15 15 0 0 0 6.6 6.6l2.2-2.2a1 1 0 0 1 1-.25 11.4 11.4 0 0 0 3.6.57 1 1 0 0 1 1 1V20a1 1 0 0 1-1 1A17 17 0 0 1 3 4a1 1 0 0 1 1-1h3.5a1 1 0 0 1 1 1c0 1.25.2 2.45.57 3.570a1 1 0 0 1-.25 1z"/></svg>
        587-412-9065
      </li>
      <li class="contact-item">
        <svg class="contact-icon" viewBox="0 0 24 24"><circle cx="12" cy="12" r="10" fill="none" stroke="var(--brand-red)" stroke-width="2.4"/><path d="M2 12h20M12 2c3 3 3 17 0 20M12 2c-3 3-3 17 0 20" fill="none" stroke="var(--brand-red)" stroke-width="2"/></svg>
        www.colinvardek.ca
      </li>
      <li class="contact-item">
        <svg class="contact-icon" viewBox="0 0 24 24"><rect x="2" y="5" width="20" height="14" rx="2" fill="var(--brand-red)"/><path d="M3 6l9 7 9-7" fill="none" stroke="var(--card-black)" stroke-width="2"/></svg>
        colinvardek@mailora.com
      </li>
    </ul>
  </section>

</main>
</body>
</html>
```